Various Designs

We need various designs for our new hand disinfectant dispensers that feature three extra-large windows that allow users to customize the appearance simply by changing the graphics.
Each dispenser has one window at the front and one on each side. The front window can have two different sizes. Please refer to attached zip file named Dispenser_Design_Templates.
The designs should be fresh and of high quality. Please don't just place a photo and spam me.
The design should also contain our logo (PVM Switzerland - is included in the template).
The design should further be professional enough for a medical and public setting. The dispensers will be used in hospitals, medical facilities, old pension homes, schools, restaurants, kitchens, public places etc.
We value creativity a lot!
It would be great if the dispenser features a slogan such as "Hand Hygiene Saves Lives". I have added a number of slogans at the end of this description.
Do not use dark colors such as brown. These colors do not stand for hygiene. You can use black but only in conjunction with a bright color.
The following files contain designs that I like:
- 01w
- velunadecor
- worldwide
- IMG_0137
Slogans:
- Hand Hygiene Saves Lives
- Did you wash your hands?
- Did you disinfect your hands?
- Protect Yourself and Your Patients
- Healthy Hands Start Here
- Hand Hygiene We Love... We Care... We Share...
- Clean hands prevent germs from spreading.
- Practice Good Hand Hygiene
- Save Lives: Clean Your Hands
- Save Lives: Disinfect Your Hands
- Washing Hands Saves Lives
- Wash Your Hands Please
- Be aware…..!!!!! Wash with care…..!!!!!
- Hand Hygiene Station
- Hand Hygiene Share your care, not your germs
- Good Hand Hygiene It's Critical Sanitize Wash Moisturize
- Disinfect (image of a hand)
- Clean (image of a hand)
- No Water? No Problem. Waterless Hand Rub. Keep it Handy.
- Wash your hands! If not for yourself, then do it for them.
- Practice good hygiene - it-s contagious!
- Be aware, wash with care!
- Filthy fingers forecast sickness and sadness.
- Hand Hygiene The power is in your hands
- Bury the germ, Wash your hands
- Sanitize your hands and support our clean hands initiative
- Sanitize your hands. Together we can make a difference.
- You are grand if you wash your hand.
- Holding hands feels better when they’re clean.
- Be wise wash hands often.
- Wash those germs away!!!
- Your Hands Can Be Dangerous. Disinfect them to keep germs away.
- Ten out of ten patients prefer care from clean hands.
- Safety first, disinfect and protect
- It’s universal- handwashing every patient every time!
- Infection control is in your hands.
- Make your intention prevention. Wash your hands

```html
<!DOCTYPE html>
<html lang="en">
<head>
<meta charset="utf-8">
<title>PVM Switzerland – Hand Hygiene Saves Lives dispenser window</title>
<link rel="stylesheet" href="https://fonts.googleapis.com/css2?family=Oswald:wght@400;500;600&display=swap">
<style>
  :root {
    --page-bg: #ffffff;
    --header-white: #ffffff;
    --brand-blue: #1d5a96;
    --rule-blue: #1d4f8c;
    --leaf-light: #e4f0a0;
    --leaf-mid: #b8d448;
    --leaf-deep: #8fb62a;
    --grass: #5f9e1c;
    --slogan: #f7f9ee;
    --slogan-shadow: rgba(70, 100, 10, 0.45);
  }
  html, body {
    margin: 0;
    padding: 0;
    width: 823px;
    height: 1200px;
    overflow: hidden;
    background: var(--page-bg);
  }
  .dispenser-window {
    display: block;
    width: 823px;
    height: 1200px;
  }
  .brand-name {
    font-family: "Oswald", sans-serif;
    font-weight: 400;
    fill: var(--brand-blue);
  }
  .slogan {
    font-family: "Oswald", sans-serif;
    font-weight: 600;
    fill: var(--slogan);
    text-anchor: middle;
    filter: drop-shadow(0 3px 4px var(--slogan-shadow));
  }
  .slogan-lead { font-size: 64px; letter-spacing: 1px; }
  .slogan-main { font-size: 150px; letter-spacing: 2px; }
</style>
</head>
<body>
<svg class="dispenser-window" viewBox="0 0 823 1200" xmlns="http://www.w3.org/2000/svg">
  <defs>
    <clipPath id="window-shape">
      <path d="M152 100 Q152 60 192 60 L632 60 Q672 60 672 100 L652 1090 Q651 1140 602 1140 L222 1140 Q173 1140 172 1090 Z"/>
    </clipPath>
    <linearGradient id="nature-tones" x1="0" y1="0" x2="0" y2="1">
      <stop offset="0" stop-color="var(--leaf-light)"/>
      <stop offset="0.3" stop-color="var(--leaf-mid)"/>
      <stop offset="0.75" stop-color="var(--leaf-deep)"/>
      <stop offset="1" stop-color="var(--grass)"/>
    </linearGradient>
  </defs>

  <g clip-path="url(#window-shape)">
    <rect class="nature-backdrop" x="140" y="230" width="550" height="920"
          fill="url(#nature-tones)" role="img"
          aria-label="Sunlit fresh green leaves over soft bokeh light, with a strip of green grass along the bottom"/>

    <path class="header-band" d="M140 40 L690 40 L690 226 Q420 236 140 256 Z" fill="var(--header-white)"/>
    <path class="header-rule" d="M140 256 Q420 236 690 226" fill="none" stroke="var(--rule-blue)" stroke-width="6"/>

    <text class="brand-name" x="196" y="180" font-size="82" letter-spacing="10">PVM</text>
    <text class="brand-name" x="470" y="170" font-size="36">Switzerland</text>

    <text class="slogan slogan-lead" x="412" y="560">HAND HYGIENE</text>
    <text class="slogan slogan-main" x="412" y="710">SAVES</text>
    <text class="slogan slogan-main" x="412" y="860">LIVES</text>
  </g>
</svg>
</body>
</html>
```